Estate Planning Law Firm opening new branch in Florida

I am an experienced estate planning attorney that recently relocated to Florida. Looking for a banner Ad to place on platforms such as HomeLane, Chatterbox and Picturely to create publicity for firm and new leads.

```html
<!DOCTYPE html>
<html lang="en">
<head>
<meta charset="UTF-8">
<title>Serenova – Estate And Financial Planning</title>
<link rel="stylesheet" href="https://fonts.googleapis.com/css2?family=Lora:wght@700&family=Roboto:wght@400;500&display=swap">
<style>
  :root {
    --ink: #2c3a4b;
    --teal: #1d6a6c;
    --body: #666b70;
    --muted: #a3a6a9;
    --dot: #c4c6c8;
    --paper: #ffffff;
  }
  * { margin: 0; padding: 0; box-sizing: border-box; }
  html, body { width: 1200px; height: 628px; overflow: hidden; background: var(--paper); }
  .banner { position: relative; width: 1200px; height: 628px; background: var(--paper); font-family: "Roboto", Arial, sans-serif; }

  .brand { position: absolute; left: 100px; top: 28px; display: flex; align-items: center; gap: 10px; }
  .brand-square { width: 20px; height: 20px; background: var(--teal); }
  .brand-name { font-family: "Lora", Georgia, serif; font-weight: 700; font-size: 26px; color: var(--ink); letter-spacing: 0.5px; }

  .dots { position: absolute; display: grid; }
  .dots span { border-radius: 50%; background: var(--dot); }
  .dots-top { left: 471px; top: 6px; grid-template-columns: repeat(4, 9px); gap: 15px 15px; }
  .dots-top span { width: 9px; height: 9px; }
  .dots-mid { left: 100px; top: 470px; grid-template-columns: repeat(6, 7px); gap: 9px 11px; }
  .dots-mid span { width: 7px; height: 7px; }
  .dots-teal { left: 580px; top: 473px; grid-template-columns: repeat(6, 4px); gap: 6px 6px; }
  .dots-teal span { width: 4px; height: 4px; background: var(--teal); }

  .rule-vertical { position: absolute; left: 573px; top: 30px; width: 5px; height: 149px; background: var(--ink); }

  .headline { position: absolute; left: 100px; top: 112px; font-family: "Lora", Georgia, serif; font-weight: 700; font-size: 69px; line-height: 89px; color: var(--ink); }
  .headline-rule { position: absolute; left: 100px; top: 304px; width: 130px; height: 4px; background: var(--teal); }

  .mission { position: absolute; left: 100px; top: 343px; width: 440px; font-size: 17px; line-height: 30px; color: var(--body); }

  .close-mark { position: absolute; left: 224px; top: 469px; }

  .contact { position: absolute; left: 100px; list-style: none; }
  .contact li { display: flex; align-items: center; gap: 7px; font-size: 15px; color: var(--ink); height: 38px; }
  .contact a { color: var(--teal); text-decoration: none; }
  .contact { top: 525px; }

  .photo { position: absolute; left: 600px; top: 0; width: 600px; height: 490px;
    background: linear-gradient(160deg, #6f6a60 0%, #b5ab9a 25%, #d8d3cb 45%, #a89e8c 65%, #c9c5bf 82%, #8f8677 100%); }

  .service { position: absolute; right: 123px; top: 512px; text-align: right; }
  .service h2 { font-family: "Lora", Georgia, serif; font-weight: 700; font-size: 25px; color: var(--ink); margin-bottom: 16px; }
  .service p { font-size: 16px; line-height: 24px; color: var(--muted); }
  .service-rule { position: absolute; left: 1095px; top: 527px; width: 4px; height: 78px; background: var(--teal); }
</style>
</head>
<body>
<main class="banner">
  <div class="brand"><span class="brand-square"></span><span class="brand-name">SERENOVA</span></div>

  <div class="dots dots-top"><span></span><span></span><span></span><span></span><span></span><span></span><span></span><span></span></div>
  <div class="rule-vertical"></div>

  <h1 class="headline">Welcome To<br>Serenova</h1>
  <div class="headline-rule"></div>

  <p class="mission">Where our mission is to bring peace of mind to working families through comprehensive estate planning, wealth management, and tax planning services.</p>

  <div class="dots dots-mid"><span></span><span></span><span></span><span></span><span></span><span></span><span></span><span></span><span></span><span></span><span></span><span></span></div>
  <svg class="close-mark" width="22" height="22" viewBox="0 0 22 22" aria-hidden="true">
    <path d="M3 3 L19 19 M19 3 L3 19" stroke="#c4c6c8" stroke-width="5" stroke-linecap="square"/>
  </svg>

  <ul class="contact">
    <li>
      <svg width="12" height="12" viewBox="0 0 12 12" aria-hidden="true"><rect width="12" height="12" rx="2" fill="#1d6a6c"/><path d="M3.4 2.6 L4.8 2.6 L5.4 4.4 L4.5 5.1 Q5.3 6.8 6.9 7.5 L7.6 6.6 L9.4 7.2 L9.4 8.6 Q9.4 9.4 8.6 9.4 Q3.2 9 2.6 3.4 Q2.6 2.6 3.4 2.6Z" fill="#fff"/></svg>
      <span>Phone Call: <a href="tel:5550142290">(555) 014-2290</a></span>
    </li>
    <li>
      <svg width="13" height="10" viewBox="0 0 13 10" aria-hidden="true"><rect width="13" height="10" rx="1" fill="#1d6a6c"/><path d="M1 1.5 L6.5 5.5 L12 1.5" stroke="#fff" stroke-width="1.2" fill="none"/></svg>
      <span>Send Email: <a href="mailto:hello@serenova.law">hello@serenova.law</a></span>
    </li>
  </ul>

  <div class="photo" role="img" aria-label="Upward view of tall marble columns with ornate carved capitals and coffered ceiling of a classical courthouse, with a hanging lantern"></div>

  <div class="dots dots-teal"><span></span><span></span><span></span><span></span><span></span><span></span><span></span><span></span><span></span><span></span><span></span><span></span><span></span><span></span><span></span><span></span><span></span><span></span><span></span><span></span><span></span><span></span><span></span><span></span></div>

  <section class="service">
    <h2>Estate And Financial Planning</h2>
    <p>Ensure peace of mind knowing that your estate planning, tax, and<br>financial professionals are all working in your best interest.</p>
  </section>
  <div class="service-rule"></div>
</main>
</body>
</html>
```